New Payments Start-up requires Logo, Style Guide and Web Site Design

We need a logo, style guide (colour templates etc.) and marketing web-site (HTML/CSS styling) for Fenwu, a new account-to-account payment product for use in the Single European Payment Area (SEPA).

The design is for the product only, not a company brand. We're looking for basic palette and style guidelines also. The web site need only be a basic responsive cross-platform design and layout. We will produce our own content.

We have no requirements for specific colours or logo styles. It is a financial product, however, so should not appear too quirky or untrustworthy.

The product is still in the early phases of development, so we're not able to provide pictures or other content.

As a little more detail on how things work, though, our end customers will arrive at our site through redirection from our merchant partners (a number of whom are large multi-national companies) who have offered our services as an alternative to credit card payments. They will be able to set up a SEPA direct debit mandate online in just a few pages, secure that with a password and use it to pay both immediately and in future with a simple confirmation of the password… a quick, easy checkout.

Because we work with large customer in the payments space, whilst we’d like the brand to be modern and appealing, it has to engender trust and stability. Whilst this product is new and in start-up phase, our company has been in alternative payments for nearly 10 years and have strong products in Europe in the Pre-Paid Zelo/TrevinCard and Voucher space. We'd like to treat this separately, however, which is why we've briefed accordingly.

Reason: Apologies for the extension, but I had a couple of designers contact me to say they had completed work but were unable to submit because time ran out. I'll only extend this once, though, because we need to get cracking on the project. Many thanks Jem

Target Market(s)

European alternative payment customers

Industry/Entity Type

Financial

Logo Text

fenwu

Coding

Coded - Design and coding required

Number of Pages Required

1 page

Font styles to use
Sans Serif

```html
<!DOCTYPE html>
<html lang="en">
<head>
<meta charset="utf-8">
<title>Fenwu – SEPA account-to-account payments</title>
<link href="https://fonts.googleapis.com/css2?family=Lato:wght@400;700&display=swap" rel="stylesheet">
<style>
:root{
  --brand-blue:#0b68ab;
  --nav-active:#1a9bf0;
  --accent-orange:#e8821c;
  --ink:#333333;
  --ink-soft:#555555;
  --panel-grey:#f6f6f6;
  --band-grey:#ececec;
  --line-grey:#c9c9c9;
  --white:#ffffff;
  --hero-warm:#efe6da;
}
*{margin:0;padding:0;box-sizing:border-box}
html,body{width:857px;height:1200px;overflow:hidden}
body{position:relative;font-family:'Lato',sans-serif;color:var(--ink);background:var(--white)}
.abs{position:absolute}

.site-header{left:0;top:0;width:857px;height:387px;background:var(--brand-blue)}
.brand-name{left:70px;top:12px;font-size:26px;font-weight:700;color:var(--white);letter-spacing:.3px}
.main-nav{left:318px;top:19px;display:flex;font-size:9.5px}
.main-nav a{color:var(--white);text-decoration:none;height:20px;line-height:20px;padding:0 9px;margin-right:11px}
.main-nav a.is-active{background:var(--nav-active)}
.main-nav a.login{background:var(--accent-orange);margin-right:0;margin-left:-5px}

.hero{left:70px;top:57px;width:717px;height:330px;overflow:hidden}
.hero-photo{position:absolute;inset:0;background:linear-gradient(135deg,var(--hero-warm) 0%,#f7f3ee 50%,var(--white) 100%)}
.hero-arrow{width:26px;height:26px;border-radius:50%;top:153px;display:flex;align-items:center;justify-content:center}
.hero-arrow.prev{left:15px;background:rgba(0,0,0,.15)}
.hero-arrow.next{left:674px;background:rgba(255,255,255,.85)}
.hero-caption{color:var(--white);font-size:12px;height:29px;line-height:29px;padding:0 7px;right:51px;white-space:nowrap}
.hero-caption.line-1{top:226px;background:rgba(43,112,170,.85)}
.hero-caption.line-2{top:257px;background:rgba(30,30,30,.85)}

.welcome{left:0;top:387px;width:857px;height:175px;background:var(--panel-grey);text-align:center}
.section-title{font-size:19px;font-weight:700;color:var(--ink);width:100%;text-align:center}
.welcome .section-title{top:21px}
.welcome-text{left:84px;top:54px;width:690px;font-size:8.8px;line-height:13.5px;color:var(--ink-soft)}
.btn{top:129px;height:23px;line-height:23px;width:70px;font-size:9.2px;color:var(--white);text-align:center}
.btn.read-more{left:356px;background:var(--brand-blue)}
.btn.join-now{left:430px;background:var(--accent-orange)}

.how-we-work .section-title{top:585px}
.how-intro{left:170px;top:618px;width:517px;text-align:center;font-size:9.3px;line-height:13.5px;color:var(--ink-soft)}
.step{top:665px;width:218px;text-align:center}
.step-icon{width:94px;height:94px;border:1px solid #777;border-radius:50%;margin:0 auto;display:flex;align-items:center;justify-content:center}
.step-title{font-size:11.3px;font-weight:700;line-height:14px;margin-top:12px;height:28px;display:flex;align-items:flex-start;justify-content:center}
.step-text{font-size:8.2px;line-height:11.6px;color:var(--ink);margin-top:11px}
.divider{left:70px;top:883px;width:717px;border-top:1px dotted var(--line-grey)}

.partners .section-title{top:904px}
.partner-badge{top:955px;width:104px;height:80px;border:1px solid #e7e7e7;display:flex;align-items:center;justify-content:center}
.partner-arrow{top:982px}

.accept-band{left:0;top:1085px;width:857px;height:57px;background:var(--band-grey)}
.accept-label{left:270px;top:1104px;font-size:15px;font-weight:700;color:var(--ink)}
.pay-card{top:1104px;width:36px;height:22px;border:1px solid #d4d4d4;background:var(--white);font-size:7px;font-weight:700;display:flex;align-items:center;justify-content:center;color:var(--brand-blue)}

.site-footer{left:0;top:1142px;width:857px;height:58px;background:var(--brand-blue)}
.social-dot{top:1165px;width:13px;height:13px;border-radius:50%;background:#c8d9e8}
.copyright{right:73px;top:1165px;font-size:10px;color:#dce8f2}
</style>
</head>
<body>

<header class="site-header abs">
  <div class="brand-name abs">Fenwu</div>
  <nav class="main-nav abs">
    <a class="is-active" href="#">Home</a>
    <a href="#">About Us</a>
    <a href="#">Services</a>
    <a href="#">Methods</a>
    <a href="#">Partners</a>
    <a href="#">Contact Us</a>
    <a class="login" href="#">Login / Register</a>
  </nav>
  <section class="hero abs">
    <div class="hero-photo" role="img" aria-label="Photo of a hand holding a payment card while tapping a tablet screen"></div>
    <div class="hero-arrow prev abs"><svg width="10" height="12" viewBox="0 0 10 12"><path d="M7 1 2 6l5 5" stroke="#fff" stroke-width="2" fill="none"/></svg></div>
    <div class="hero-arrow next abs"><svg width="10" height="12" viewBox="0 0 10 12"><path d="M3 1l5 5-5 5" stroke="#666" stroke-width="2" fill="none"/></svg></div>
    <div class="hero-caption line-1 abs">We are a new account-to-account payment product for</div>
    <div class="hero-caption line-2 abs">use in the Single European Payment Area (SEPA).</div>
  </section>
</header>

<section class="welcome abs">
  <h2 class="section-title abs">Welcome</h2>
  <p class="welcome-text abs">Integer vel iaculis diam, id vehicula enim. Aliquam tincidunt ut dolor et facilisis. Phasellus sed ultricies arcu, id commodo nisl. Vestibulum convallis ut elit in posuere. Sed sit amet nulla vitae augue ultricies varius. Duis tempor metus et accumsan maximus. Nullam a lectus metus. Aenean posuere id ex eu convallis. Suspendisse a ornare enim. Donec fermentum dolor gravida turpis placerat, sed accumsan risus sollicitudin. Proin lacus sem, feugiat sit amet iaculis non, elementum eget sapien. Integer nisl sem, blandit quis sapien nec, convallis cursus est. Cras a tellus gravida, suscipit est sit amet, consectetur nunc. Nulla facilisis ex sagittis, varius tellus sed, lacinia lacus.</p>
  <a class="btn read-more abs">Read More</a>
  <a class="btn join-now abs">Join Now</a>
</section>

<section class="how-we-work">
  <h2 class="section-title abs">How We Work</h2>
  <p class="how-intro abs">Our company has been in alternative payments for nearly 10 years and have strong products in Europe in the Pre-Paid Zelo/TrevinCard and Voucher space</p>

  <div class="step abs" style="left:70px">
    <div class="step-icon"><svg width="32" height="26" viewBox="0 0 32 26"><path d="M2 7h7c6 0 8 12 14 12h5M2 19h7c3 0 4-3 6-6M19 9c1-1 2-2 4-2h5" stroke="#3a3a3a" stroke-width="3.5" fill="none"/><path d="M26 2l5 5-5 5zM26 14l5 5-5 5z" fill="#3a3a3a"/></svg></div>
    <h3 class="step-title">Redirection From our<br>Merchant Partners</h3>
    <p class="step-text">Proin quis enim non nisl finibus euismod. Aenean molestie tempor neque et facilisis. Nullam gravida bibendum augue, non rhoncus nulla ornare a. Pellentesque egestas mauris eu neque molestie lacinia.</p>
  </div>
  <div class="step abs" style="left:319px">
    <div class="step-icon"><svg width="32" height="26" viewBox="0 0 32 26"><rect x="1.5" y="1.5" width="29" height="23" rx="2" stroke="#3a3a3a" stroke-width="3" fill="none"/><rect x="1.5" y="7" width="29" height="4" fill="#3a3a3a"/><rect x="5" y="17" width="5" height="2.5" fill="#3a3a3a"/><rect x="12" y="17" width="6" height="2.5" fill="#3a3a3a"/></svg></div>
    <h3 class="step-title">Pay With Us</h3>
    <p class="step-text">Proin quis enim non nisl finibus euismod. Aenean molestie tempor neque et facilisis. Nullam gravida bibendum augue, non rhoncus nulla ornare a. Pellentesque egestas mauris eu neque molestie lacinia.</p>
  </div>
  <div class="step abs" style="left:568px">
    <div class="step-icon"><svg width="28" height="22" viewBox="0 0 28 22"><path d="M3 11l8 8L25 4" stroke="#3a3a3a" stroke-width="5" fill="none"/></svg></div>
    <h3 class="step-title">Payment Successful</h3>
    <p class="step-text">Proin quis enim non nisl finibus euismod. Aenean molestie tempor neque et facilisis. Nullam gravida bibendum augue, non rhoncus nulla ornare a. Pellentesque egestas mauris eu neque molestie lacinia.</p>
  </div>
  <div class="divider abs"></div>
</section>

<section class="partners">
  <h2 class="section-title abs">Our Partners</h2>
  <svg class="partner-arrow abs" style="left:30px" width="10" height="18" viewBox="0 0 10 18"><path d="M8 2 2 9l6 7" stroke="#bbb" stroke-width="2" fill="none"/></svg>
  <div class="partner-badge abs" style="left:70px"><svg width="60" height="30"><rect x="1" y="1" width="58" height="28" fill="#dcdcdc"/></svg></div>
  <div class="partner-badge abs" style="left:193px"><svg width="64" height="48"><ellipse cx="32" cy="24" rx="31" ry="22" fill="none" stroke="#222" stroke-width="2"/></svg></div>
  <div class="partner-badge abs" style="left:315px"><svg width="64" height="56"><circle cx="32" cy="28" r="26" fill="#dedede"/></svg></div>
  <div class="partner-badge abs" style="left:437px"><svg width="64" height="40"><rect x="8" y="2" width="48" height="36" fill="none" stroke="#cfcfcf" stroke-width="2"/></svg></div>
  <div class="partner-badge abs" style="left:560px"><svg width="56" height="52"><rect x="2" y="2" width="52" height="48" rx="10" fill="#cdcdcd"/></svg></div>
  <div class="partner-badge abs" style="left:682px"><svg width="80" height="36"><rect x="2" y="8" width="76" height="20" fill="#cfcfcf"/></svg></div>
  <svg class="partner-arrow abs" style="left:813px" width="10" height="18" viewBox="0 0 10 18"><path d="M2 2l6 7-6 7" stroke="#bbb" stroke-width="2" fill="none"/></svg>
</section>

<section class="accept-band abs"></section>
<div class="accept-label abs">We Accept:</div>
<div class="pay-card abs" style="left:370px">Zelo</div>
<div class="pay-card abs" style="left:413px">Corvane</div>
<div class="pay-card abs" style="left:456px">Lumiq</div>
<div class="pay-card abs" style="left:499px;font-size:5.5px">TrevinCard</div>
<div class="pay-card abs" style="left:542px">Paxo</div>

<footer class="site-footer abs"></footer>
<span class="social-dot abs" style="left:68px"></span>
<span class="social-dot abs" style="left:99px"></span>
<span class="social-dot abs" style="left:127px"></span>
<span class="social-dot abs" style="left:154px"></span>
<div class="copyright abs">© yoursite - All Rights Reserved</div>

</body>
</html>
```